New florist business website design

Number 1 want is an easy to navigate & check out website
Needs to be beautiful and eye catching as well.
This is an online only business (no shop front)
Rustic and blush pinks, neutrals, woods, leaves
Customers need to be able to go onto my website, select something they want to buy but have the option to use a drop down box to change colours of the flowers, or add notes to make changes to the arrangement

Industry/Entity Type

Florist

Coding

Coded - Design and coding required

Number of Pages Required

5+ page

Colors
f9d9e8
fff2ec
fffefc

Requirements
Must have
• Drop down menu to take you to other pages for Arrangements, bouquets, everlasting arrangements, gifts, contact
Be able to purchase and “add to basket”
Checkout page
Nice to have
• Be able to add my own photos once I’ve taken new ones
Should not have
• Tacky images or clip art

```html
<!DOCTYPE html>
<html lang="en">
<head>
<meta charset="utf-8">
<title>Bloom &amp; Bramble — Florist</title>
<link href="https://fonts.googleapis.com/css2?family=Jost:wght@300;400;500;600&family=Allura&display=swap" rel="stylesheet">
<style>
:root{
  --blush:#f9d9e8;
  --cream:#fff2ec;
  --paper:#fffefc;
  --rose:#f3c1d3;
  --deep-rose:#d9678f;
  --ink:#2a2426;
  --muted:#7d7276;
  --line:#3a3234;
  --leaf:#8cc63f;
}
*{box-sizing:border-box;margin:0;padding:0}
html,body{width:1200px;height:4060px;overflow:hidden}
body{font-family:'Jost',sans-serif;color:var(--ink);background:linear-gradient(180deg,var(--paper) 0%,#fdf0f3 30%,var(--paper) 50%,#fde9ef 75%,#fbe3ea 100%);position:relative}
.abs{position:absolute}
.script{font-family:'Allura',cursive;font-weight:400}
.btn{position:absolute;border:2px solid var(--line);border-radius:40px;background:var(--paper);font-size:15px;font-weight:500;letter-spacing:1px;text-transform:uppercase;display:flex;align-items:center;justify-content:center;color:var(--ink)}
.photo{position:absolute}
.lorem{font-size:15px;line-height:1.55;color:var(--muted)}

/* header */
.hero{position:absolute;left:0;top:0;width:1200px;height:560px;background:linear-gradient(90deg,#fde7ee 0%,#fff 45%,#fde4ec 100%)}
.hero-photo{right:0;top:0;width:560px;height:540px;background:radial-gradient(circle at 55% 38%,#e8457f 0%,#f27aa6 28%,#f7b9cf 55%,#fde4ec 80%)}
.hero-left-photo{left:0;top:0;width:300px;height:380px;background:radial-gradient(circle at 20% 20%,#f6c3d4 0%,#fbe2ea 55%,rgba(255,255,255,0) 80%)}
.nav a{position:absolute;top:56px;font-size:16px;color:var(--ink);text-decoration:none}
.brand{position:absolute;left:540px;top:30px;width:120px;text-align:center;font-size:18px;font-weight:500;color:var(--ink);line-height:1.1}
.brand-ring{position:absolute;left:575px;top:18px;width:50px;height:50px;border:1.5px solid var(--ink);border-radius:50%}
.hero h1{position:absolute;left:120px;top:282px;font-size:30px;font-weight:400;letter-spacing:1px}
.hero .script{position:absolute;left:118px;top:318px;font-size:96px;line-height:1}
.dots{position:absolute;display:flex;gap:10px}
.dots span{width:10px;height:10px;border-radius:50%;background:#c8bcc0}
.dots span.on{background:var(--ink)}

/* section titles */
.kicker{position:absolute;left:0;width:1200px;text-align:center;font-size:19px}
.title-script{position:absolute;left:0;width:1200px;text-align:center;font-size:66px;line-height:1}
.title-serif{position:absolute;left:0;width:1200px;text-align:center;font-size:44px;font-weight:400}

/* products */
.product{position:absolute;top:912px;width:232px;height:408px;text-align:center}
.product.featured{background:var(--cream);box-shadow:0 10px 30px rgba(200,140,160,.25);border-radius:6px}
.product .photo{left:66px;top:40px;width:100px;height:180px;border-radius:50px 50px 20px 20px}
.product .name{position:absolute;left:0;top:246px;width:232px;font-size:19px}
.product .price{position:absolute;left:0;top:278px;width:232px;font-size:36px;font-weight:500}
.add-cart{position:absolute;left:50px;top:340px;width:132px;height:40px;border:1.5px solid var(--line);border-radius:20px;font-size:13px;display:flex;align-items:center;justify-content:center;gap:8px;background:var(--paper)}

/* welcome */
.welcome-text{position:absolute;left:596px;top:1710px;width:520px}
.welcome-text h2{font-size:44px;font-weight:500;line-height:1.2}
.welcome-text p{margin-top:20px}

/* blog */
.post{position:absolute;top:2392px;width:320px;text-align:center}
.post .photo{position:relative;width:320px;height:228px;border-radius:4px}
.post .date{position:absolute;left:128px;top:196px;width:64px;height:64px;border-radius:50%;background:var(--paper);font-size:12px;line-height:1.2;display:flex;flex-direction:column;align-items:center;justify-content:center;box-shadow:0 3px 10px rgba(0,0,0,.08)}
.post h3{margin-top:56px;font-size:30px;font-weight:500}
.post p{margin-top:14px;padding:0 6px}
.post .more{display:block;margin-top:14px;font-size:15px;color:var(--muted)}

/* testimonials */
.quote{position:absolute;left:210px;top:3126px;width:780px;text-align:center;font-size:15px;line-height:1.6;color:var(--ink)}
.qmark{position:absolute;font-size:64px;font-weight:600;line-height:1}

/* newsletter */
.news h2{position:absolute;left:72px;top:3392px;font-size:32px;font-weight:500}
.news p{position:absolute;left:72px;top:3444px;width:520px}
.news .field{position:absolute;left:672px;top:3426px;width:300px;height:46px;border:1.5px solid var(--line);border-radius:24px;font-size:14px;color:var(--muted);padding:13px 20px}
.news .subscribe{left:984px;top:3426px;width:136px;height:46px}

/* footer */
.footer-col{position:absolute;top:3700px}
.footer-col h4{font-size:32px;font-weight:400;margin-bottom:34px}
.footer-col li{list-style:none;font-size:15px;line-height:1.55}
.contact-line{display:flex;gap:14px;align-items:flex-start;font-size:15px;line-height:1.5;margin-bottom:14px}
.socials{position:absolute;left:72px;top:3960px;display:flex;gap:20px;font-size:13px;font-weight:500}
.thumbs{position:absolute;left:824px;top:3788px;display:grid;grid-template-columns:repeat(3,88px);gap:14px}
.thumbs div{height:76px;border-radius:2px}
.bottom-bar{position:absolute;left:0;top:4020px;width:1200px;height:40px;background:var(--rose);display:flex;align-items:center;justify-content:space-between;padding:0 72px;font-size:13px}
.pay{display:flex;gap:8px}
.pay span{width:44px;height:26px;border-radius:3px;background:var(--paper)}
</style>
</head>
<body>

<!-- HERO -->
<section class="hero">
  <div class="photo hero-left-photo" role="img" aria-label="Soft pink flower petals fading into the background"></div>
  <div class="photo hero-photo" role="img" aria-label="Bouquet of pink peonies in a glass vase"></div>

  <svg class="abs" style="left:116px;top:56px" width="60" height="22" viewBox="0 0 60 22" aria-hidden="true">
    <path d="M2 4h18M2 11h14M2 18h18" stroke="#2a2426" stroke-width="2" fill="none"/>
    <circle cx="46" cy="9" r="6.5" stroke="#2a2426" stroke-width="2" fill="none"/>
    <path d="M51 14l5 5" stroke="#2a2426" stroke-width="2"/>
  </svg>
  <nav class="nav">
    <a style="left:334px">Shop</a>
    <a style="left:420px">About</a>
    <a style="left:720px">Blog</a>
    <a style="left:808px">Contact</a>
  </nav>
  <div class="brand-ring"></div>
  <div class="brand" style="top:72px;font-size:17px">Bloom &amp; Bramble</div>
  <svg class="abs" style="left:1018px;top:52px" width="70" height="26" viewBox="0 0 70 26" aria-hidden="true">
    <circle cx="9" cy="8" r="5" stroke="#2a2426" stroke-width="1.8" fill="none"/>
    <path d="M1 22c1-6 5-8 8-8s7 2 8 8" stroke="#2a2426" stroke-width="1.8" fill="none"/>
    <path d="M15 4l4 4" stroke="#2a2426" stroke-width="1.8"/>
    <circle cx="56" cy="13" r="10" stroke="#2a2426" stroke-width="1.8" fill="none"/>
    <path d="M51 10h10l-1 6h-8z" stroke="#2a2426" stroke-width="1.5" fill="none"/>
  </svg>

  <h1>GORGEOUS FLOWERS FOR YOUR</h1>
  <div class="script">Special Events</div>
  <div class="btn" style="left:120px;top:424px;width:124px;height:46px;font-size:13px">Shop now</div>
</section>
<div class="dots" style="left:580px;top:602px"><span class="on"></span><span></span><span></span></div>

<!-- FEATURED PRODUCTS -->
<div class="kicker" style="top:718px">Wounderful Flowers</div>
<div class="title-script" style="top:752px">Feature Products</div>
<svg class="abs" style="left:560px;top:830px" width="80" height="20" viewBox="0 0 80 20" aria-hidden="true">
  <path d="M4 10h30M46 10h30" stroke="#2a2426" stroke-width="1.2"/>
  <circle cx="40" cy="10" r="4" stroke="#2a2426" stroke-width="1.2" fill="none"/>
</svg>

<svg class="abs" style="left:52px;top:1090px" width="20" height="30" viewBox="0 0 20 30" aria-hidden="true"><path d="M15 3L4 15l11 12" stroke="#2a2426" stroke-width="2" fill="none"/></svg>
<svg class="abs" style="left:1116px;top:1090px" width="20" height="30" viewBox="0 0 20 30" aria-hidden="true"><path d="M5 3l11 12L5 27" stroke="#2a2426" stroke-width="2" fill="none"/></svg>

<div class="product" style="left:144px">
  <div class="photo" role="img" aria-label="Bouquet of red roses in pink wrapping" style="background:linear-gradient(180deg,#d3213a 0%,#e14b61 45%,#f3bcca 100%)"></div>
  <div class="name">Name of product # 01</div><div class="price">$40</div>
</div>
<div class="product featured" style="left:360px">
  <div class="photo" role="img" aria-label="Pink mixed bouquet wrapped in paper" style="background:linear-gradient(180deg,#e9789c 0%,#f4a9c0 50%,#f6cfdc 100%)"></div>
  <div class="name">Name of product # 01</div><div class="price">$40</div>
  <div class="add-cart">Add To Cart
    <svg width="14" height="14" viewBox="0 0 14 14" aria-hidden="true"><path d="M2 4h10l-1 8H3z" stroke="#2a2426" stroke-width="1.3" fill="none"/><path d="M5 4a2 2 0 0 1 4 0" stroke="#2a2426" stroke-width="1.3" fill="none"/></svg>
  </div>
</div>
<div class="product" style="left:624px">
  <div class="photo" role="img" aria-label="Bunch of red and pink tulips" style="background:linear-gradient(180deg,#d0305a 0%,#e76c8a 40%,#9bbf6e 100%)"></div>
  <div class="name">Name of product # 01</div><div class="price">$40</div>
</div>
<div class="product" style="left:864px">
  <div class="photo" role="img" aria-label="Bunch of white lilies with green stems" style="background:linear-gradient(180deg,#f5f3ee 0%,#e8eadf 45%,#8fb26a 100%)"></div>
  <div class="name">Name of product # 01</div><div class="price">$40</div>
</div>

<div class="btn" style="left:512px;top:1390px;width:176px;height:48px;font-size:13px">Browse more</div>

<!-- WELCOME -->
<div class="photo" role="img" aria-label="Green leaves" style="left:0;top:1360px;width:170px;height:180px;background:radial-gradient(circle at 40% 50%,#7fc13e 0%,#a7d75f 45%,rgba(255,255,255,0) 72%)"></div>
<div class="photo" role="img" aria-label="Florist market stall with flower buckets" style="left:120px;top:1628px;width:340px;height:452px;background:linear-gradient(160deg,#8a6a78 0%,#b58aa6 35%,#e8c4d2 60%,#7d8c6a 100%)"></div>
<div class="photo" role="img" aria-label="Pink and white flower arrangement" style="left:372px;top:1960px;width:220px;height:240px;border:10px solid var(--paper);background:linear-gradient(150deg,#e17ea0 0%,#f3b7c9 45%,#b7c98c 100%)"></div>
<div class="script abs" style="left:596px;top:1580px;font-size:140px;color:#f5d3df;line-height:1">Welcome</div>
<div class="welcome-text">
  <h2>Exclusive Design by<br>Best Florists</h2>
  <p class="lorem">Lorem Ipsum is simply dummy text of the printing and typesetting industry. Lorem Ipsum has been the industry's standard dummy text ever since the 1500s.</p>
</div>
<div class="btn" style="left:596px;top:1884px;width:142px;height:46px;font-size:13px">Shop now</div>
<div class="photo" role="img" aria-label="Pink and white peonies" style="left:928px;top:1800px;width:272px;height:330px;background:radial-gradient(circle at 65% 50%,#f2a8c0 0%,#f8d0dc 40%,rgba(255,255,255,0) 70%)"></div>

<!-- BLOG -->
<div class="script abs" style="left:72px;top:2262px;font-size:44px">Artistic</div>
<div class="abs" style="left:72px;top:2306px;font-size:44px">Blog Posts</div>
<div class="btn" style="left:952px;top:2310px;width:168px;height:50px;font-size:13px">Browse more</div>

<article class="post" style="left:72px">
  <div class="photo" role="img" aria-label="Pink blossom branches" style="background:linear-gradient(135deg,#f4c6d4 0%,#e9a0b8 45%,#c9d7b6 100%)">
    <div class="date"><b>june</b>5 2021</div>
  </div>
  <h3>Artcle title # 01</h3>
  <p class="lorem">Lorem Ipsum is simply dummy text of the printing and typesetting industry. Lorem Ipsum has been the industry's standard dummy text ever since the 1500s.</p>
  <span class="more">Read More »</span>
</article>
<article class="post" style="left:432px">
  <div class="photo" role="img" aria-label="Magenta and purple flowers" style="background:linear-gradient(135deg,#b03fb0 0%,#d85bc7 45%,#7c2f8e 100%)">
    <div class="date"><b>june</b>5 2021</div>
  </div>
  <h3>Artcle title # 02</h3>
  <p class="lorem">Lorem Ipsum is simply dummy text of the printing and typesetting industry. Lorem Ipsum has been the industry's standard dummy text ever since the 1500s.</p>
  <span class="more">Read More »</span>
</article>
<article class="post" style="left:792px">
  <div class="photo" role="img" aria-label="Orange and pink chrysanthemums" style="background:linear-gradient(135deg,#f0a12b 0%,#e76a3f 45%,#d96a9e 100%)">
    <div class="date"><b>june</b>5 2021</div>
  </div>
  <h3>Artcle title # 03</h3>
  <p class="lorem">Lorem Ipsum is simply dummy text of the printing and typesetting industry. Lorem Ipsum has been the industry's standard dummy text ever since the 1500s.</p>
  <span class="more">Read More »</span>
</article>

<!-- TESTIMONIALS -->
<div class="photo" role="img" aria-label="Purple bellflowers on a stem" style="left:0;top:2850px;width:220px;height:200px;background:radial-gradient(circle at 45% 55%,#6b4ca8 0%,#9c84d0 35%,rgba(255,255,255,0) 70%)"></div>
<div class="script kicker" style="top:2960px;font-size:34px">Reviews</div>
<div class="title-serif" style="top:2994px">Testimonials</div>
<div class="qmark" style="left:178px;top:3108px">“</div>
<p class="quote">Lorem Ipsum is simply dummy text of the printing and typesetting industry. Lorem Ipsum has been the industry's standard dummy text ever since the 1500s, when an unknown printer took a galley of type and scrambled it to make a type specimen book. It has survived not only five centuries, but also the leap into electronic typesetting, remaining essentially unchanged.</p>
<div class="qmark" style="left:994px;top:3168px">”</div>
<div class="script kicker" style="top:3208px;font-size:30px">Name</div>
<div class="dots" style="left:580px;top:3284px"><span class="on"></span><span></span><span></span></div>
<div class="photo" role="img" aria-label="Green leaves" style="left:1040px;top:3150px;width:160px;height:190px;background:radial-gradient(circle at 60% 50%,#3f8f2e 0%,#76b955 40%,rgba(255,255,255,0) 72%)"></div>

<!-- NEWSLETTER -->
<section class="news">
  <h2>Join us for our latest news updates</h2>
  <p class="lorem">Lorem Ipsum is simply dummy text of the printing and typesetting industry. Lorem Ipsum has been the industry's standard dummy text ever since the 1500s.</p>
  <div class="field">Email Address</div>
  <div class="btn subscribe">Subscribe</div>
</section>

<div class="brand-ring" style="top:3546px;width:70px;height:70px;left:565px"></div>
<div class="brand" style="top:3632px;left:520px;width:160px">Bloom &amp; Bramble</div>

<!-- FOOTER -->
<footer>
  <div class="footer-col" style="left:72px;width:260px">
    <h4>Contact info.</h4>
    <div class="contact-line">
      <svg width="14" height="18" viewBox="0 0 14 18" aria-hidden="true"><path d="M7 17s6-6 6-10A6 6 0 0 0 1 7c0 4 6 10 6 10z" fill="#2a2426"/><circle cx="7" cy="7" r="2" fill="#fffefc"/></svg>
      <span>27 Willow Lane<br>Fernvale, CA 90000</span>
    </div>
    <div class="contact-line">
      <svg width="16" height="16" viewBox="0 0 16 16" aria-hidden="true"><path d="M3 1l3 3-2 2c1 2 3 4 6 6l2-2 3 3-2 2C7 15 1 9 1 3z" fill="#2a2426"/></svg>
      <span>+1 (555) 014-7788</span>
    </div>
    <div class="contact-line">
      <svg width="16" height="14" viewBox="0 0 16 14" aria-hidden="true"><rect x="1" y="2" width="14" height="10" fill="none" stroke="#2a2426" stroke-width="1.5"/><path d="M1 2l7 6 7-6" fill="none" stroke="#2a2426" stroke-width="1.5"/></svg>
      <span>hello@bloombramble.com</span>
    </div>
  </div>
  <div class="socials"><span>Petalbook</span><span>Chirp</span><span>Gleam</span><span>Pinny</span></div>

  <div class="footer-col" style="left:356px">
    <h4>Quick links</h4>
    <ul><li>Shop</li><li>About</li><li>Blog</li><li>Contact</li><li>Arrangement</li><li>Bouquets</li><li>Everlasting arrangements</li><li>Gifts</li></ul>
  </div>
  <div class="footer-col" style="left:584px">
    <h4>Account</h4>
    <ul><li>Login</li><li>Signup</li><li>My Profile</li><li>My cart</li><li>Checkout</li><li>Return Policy</li></ul>
  </div>
  <div class="footer-col" style="left:824px">
    <h4>Follow us</h4>
  </div>
  <div class="thumbs">
    <div role="img" aria-label="Pink flower arrangement" style="background:linear-gradient(135deg,#e9a0b8,#c97a97)"></div>
    <div role="img" aria-label="Blue and white bouquet" style="background:linear-gradient(135deg,#6f86c4,#c9d3ea)"></div>
    <div role="img" aria-label="Purple flowers" style="background:linear-gradient(135deg,#8a5fb8,#c7a8df)"></div>
    <div role="img" aria-label="Pale pink roses" style="background:linear-gradient(135deg,#f1c9d6,#d9a3b5)"></div>
    <div role="img" aria-label="Blue hydrangeas" style="background:linear-gradient(135deg,#5f7fc0,#a9bce6)"></div>
    <div role="img" aria-label="Lavender bouquet" style="background:linear-gradient(135deg,#9a7cc8,#d7c6ea)"></div>
  </div>

  <div class="bottom-bar">
    <span>Copyright © 2023 Bloom &amp; Bramble | Privacy Policy</span>
    <div class="pay"><span></span><span></span><span></span><span></span><span></span></div>
  </div>
</footer>

</body>
</html>
```